FunBrixo Business Card

We need a business card design for our company. We sell construction-themed amusement rides for kids.

Contact Information for Business Card

Contact info on business card should include:
Carl Dunning
Co-Founder & COO
(833) 571-FUNBRIX
Carl@funbrixo-demo.com
www.funbrixo-demo.com

```html
<!DOCTYPE html>
<html lang="en">
<head>
<meta charset="utf-8">
<title>FunBrixo Business Card</title>
<link rel="stylesheet" href="https://fonts.googleapis.com/css2?family=Arimo:wght@400;700&display=swap">
<style>
  :root {
    --stage: #2e2e2e;
    --card: #231f20;
    --orange: #f15a24;
    --pink: #ec008c;
    --cyan: #00aeef;
    --amber: #f7a51c;
    --blue: #0067b1;
    --purple: #92278f;
    --white: #ffffff;
  }
  * { box-sizing: border-box; margin: 0; padding: 0; }
  html, body { width: 1200px; height: 866px; overflow: hidden; }
  body {
    background: var(--stage);
    font-family: "Arimo", Arial, sans-serif;
    display: flex;
    flex-direction: column;
    align-items: center;
    justify-content: center;
    gap: 52px;
  }
  .card {
    position: relative;
    width: 620px;
    height: 354px;
    background: var(--card);
    box-shadow: 0 10px 30px rgba(0,0,0,0.45);
    overflow: hidden;
  }
  .color-band {
    position: absolute;
    left: 0; right: 0; bottom: 0;
    height: 16px;
    display: flex;
  }
  .color-band span { flex: 1; }
  .color-band .c1 { background: var(--orange); }
  .color-band .c2 { background: var(--pink); }
  .color-band .c3 { background: var(--cyan); }
  .color-band .c4 { background: var(--amber); }
  .color-band .c5 { background: var(--blue); }
  .color-band .c6 { background: var(--purple); }

  .brand {
    display: flex;
    align-items: center;
    gap: 14px;
  }
  .brand-name {
    font-weight: 700;
    color: var(--orange);
    letter-spacing: 0.5px;
  }
  .brand-dot {
    border-radius: 50%;
    background: var(--purple);
  }

  /* Front */
  .card-front .brand {
    position: absolute;
    left: 0; right: 0; top: 0; bottom: 16px;
    justify-content: center;
  }
  .card-front .brand-name { font-size: 72px; }
  .card-front .brand-dot { width: 44px; height: 44px; }

  /* Back */
  .person {
    position: absolute;
    left: 44px; top: 52px;
  }
  .person-name {
    color: var(--orange);
    font-weight: 700;
    font-size: 26px;
  }
  .person-role {
    color: var(--white);
    font-size: 17px;
    margin-top: 4px;
  }
  .contact {
    position: absolute;
    left: 44px; bottom: 92px;
    color: var(--white);
    font-size: 16px;
    line-height: 1.35;
  }
  .card-back .brand {
    position: absolute;
    right: 40px; top: 130px;
  }
  .card-back .brand-name { font-size: 42px; }
  .card-back .brand-dot { width: 28px; height: 28px; }
  .website {
    position: absolute;
    right: 40px; bottom: 40px;
    color: var(--white);
    font-size: 17px;
    letter-spacing: 0.3px;
  }
  .website .accent { color: var(--orange); }
</style>
</head>
<body>
  <section class="card card-front">
    <div class="brand">
      <span class="brand-name">FunBrixo</span>
      <span class="brand-dot"></span>
    </div>
    <div class="color-band"><span class="c1"></span><span class="c2"></span><span class="c3"></span><span class="c4"></span><span class="c5"></span><span class="c6"></span></div>
  </section>

  <section class="card card-back">
    <div class="person">
      <p class="person-name">Carl Dunning</p>
      <p class="person-role">Co-Founder &amp; COO</p>
    </div>
    <div class="contact">
      <p class="phone">(833) 571-FUNBRIX</p>
      <p class="email">Carl@funbrixo-demo.com</p>
    </div>
    <div class="brand">
      <span class="brand-name">FunBrixo</span>
      <span class="brand-dot"></span>
    </div>
    <p class="website">www.<span class="accent">funbrixo-demo</span>.com</p>
    <div class="color-band"><span class="c1"></span><span class="c2"></span><span class="c3"></span><span class="c4"></span><span class="c5"></span><span class="c6"></span></div>
  </section>
</body>
</html>
```